ultra-minimalist business card

front (black background, matte):

reza t. kovin
writer | photographer
get@rezakovin.com

back (white background, matte):

a picture speaks a thousand words;
a word draws a thousand pictures.

www.rezakovin.com

all text should be small (white or silver - as long as it shows against the black - on the front; black or gray - as long as it shows against the white - on the back).

feel free to get creative in terms of arrangement, alignment, and font type, but remember, the overall style is minimalist, so nothing too fancy, please.

thanks.

```html
<!DOCTYPE html>
<html lang="en">
<head>
<meta charset="utf-8">
<title>Reza T. Kovin — Business Card</title>
<link rel="stylesheet" href="https://fonts.googleapis.com/css2?family=Barlow:wght@400;500;600&display=swap">
<style>
  :root {
    --backdrop: #e9e9ea;
    --front-dark: #3f3f40;
    --front-light: #8c8c8d;
    --front-text: #e6e6e6;
    --front-muted: #cfcfcf;
    --back-paper: #f7f7f7;
    --back-text: #3a3a3a;
    --card-shadow: rgba(0, 0, 0, 0.14);
  }
  * { margin: 0; padding: 0; box-sizing: border-box; }
  html, body {
    width: 1200px;
    height: 720px;
    overflow: hidden;
    background: var(--backdrop);
    font-family: "Barlow", "Helvetica Neue", Arial, sans-serif;
  }
  .canvas {
    position: relative;
    width: 1200px;
    height: 720px;
    display: flex;
    align-items: center;
    justify-content: center;
    gap: 60px;
  }
  .card {
    position: relative;
    width: 520px;
    height: 297px;
    box-shadow: 0 6px 18px var(--card-shadow);
  }
  /* Front side */
  .card--front {
    background: linear-gradient(200deg, var(--front-light) 0%, #6a6a6b 45%, var(--front-dark) 100%);
    color: var(--front-text);
  }
  .identity {
    position: absolute;
    left: 62px;
    top: 104px;
    text-align: right;
  }
  .identity__name {
    font-size: 34px;
    font-weight: 500;
    letter-spacing: 0.08em;
    text-transform: uppercase;
    line-height: 1;
  }
  .identity__role {
    margin-top: 4px;
    font-size: 12px;
    font-weight: 400;
    letter-spacing: 0.06em;
    color: var(--front-muted);
  }
  .contact-email {
    position: absolute;
    right: 40px;
    bottom: 26px;
    font-size: 10px;
    letter-spacing: 0.08em;
    color: var(--front-muted);
  }
  /* Back side */
  .card--back {
    background: var(--back-paper);
    color: var(--back-text);
  }
  .motto {
    position: absolute;
    left: 34px;
    bottom: 48px;
    font-size: 21px;
    font-weight: 600;
    letter-spacing: 0.07em;
    line-height: 1.12;
    text-transform: uppercase;
  }
  .website {
    position: absolute;
    left: 36px;
    bottom: 26px;
    font-size: 10px;
    font-weight: 500;
    letter-spacing: 0.12em;
    text-transform: uppercase;
  }
</style>
</head>
<body>
  <main class="canvas">
    <section class="card card--front" aria-label="Card front">
      <div class="identity">
        <h1 class="identity__name">Reza T. Kovin</h1>
        <p class="identity__role">writer | photographer</p>
      </div>
      <p class="contact-email">get@rezakovin.com</p>
    </section>

    <section class="card card--back" aria-label="Card back">
      <p class="motto">
        A picture speaks<br>
        a thousand words,<br>
        a word draws<br>
        a thousand pictures.
      </p>
      <p class="website">www.rezakovin.com</p>
    </section>
  </main>
</body>
</html>
```